Wordpress Web Design & Coding for velcorahealth.ca

We need a website for a new investment company that is visually grabbing and vibrant. We would like to see a web page that displays trust, growth and confidence. Needs to be responsive and mobile friendly for all browsers and coded for both Android & IOS.

Open to the number of pages and menu items. I selected 4 but if you feel the layout would work better with less I am open to this. Need to sell the people (management team/related businesses) and then show where the invested money will be going (upcoming projects).

Company Info:

Vel Cora is an investment company put together by a group of seasoned business professionals who have come together to combine decades of success in the real estate development, management, financing and medical services. The company will be a full service company offering turn key solutions for medical professionals.

Vel-Cora will focus on providing a full range of services via a group of distinct companies to deliver newly emerging needs of the medical community. The end goal will be to create complete solutions for individuals in the medical community. Our group has experience and success with the conceptualization, construction and financing of medical and dental clinic spaces. Vel-Cora Solutions will be established to accommodate all areas of the development and creation of clinics for medical professionals from building construction to equipment financing and administrations.

You can mention these companies and take photos from their websites. You can also use stock photos.

Our construction partner:
https://318bld.com/projects/

Our equipment leasing partner:
https://www.norvixa.com/

Our Management Team and medical partners

Gil Parish
https://www.ourfirmstance.ca/

Dietmar Vellasquin
https://www.gshdentalservices.com/about-us

PROPOSED PROJECTS (see attachment for details)
Pinegrove Business Park
Holtmere Business Park
Mt. Corwin Ridge Professional

Target Market(s)

Investors

Industry/Entity Type

Investment

Coding

Coded - Design and coding required

Number of Pages Required

4 page

Font styles to use
Sans Serif

Requirements
Must have
• Wordpress – must be both desktop and mobile friendly with fast page load speed
Ability to edit after ourselves in Wordpress
Attractive home page with logo etc.
Logo colours are: for the blue the pantone color is #0355a3
and for the green is #8cc63f

Sections, about us, what we do/services we provide, contact us

```html
<!DOCTYPE html>
<html lang="en">
<head>
<meta charset="utf-8">
<title>Vel-Cora Solutions</title>
<link rel="stylesheet" href="https://fonts.googleapis.com/css2?family=Montserrat:wght@400;500;600;700;800;900&display=swap">
<style>
:root{
  --blue:#0d4595;
  --blue-deep:#0a3a85;
  --green:#8cc63f;
  --ink:#1f2430;
  --muted:#6d7380;
  --pale:#e9f0f9;
  --ghost:#e6e8ec;
  --line:#cfd5de;
  --white:#ffffff;
}
*{box-sizing:border-box;margin:0;padding:0}
html,body{width:1200px;height:4882px;overflow:hidden}
body{position:relative;background:var(--white);font-family:"Montserrat",sans-serif;color:var(--ink)}
.abs{position:absolute}
.top-rule{left:0;top:0;width:1200px;height:4px;background:var(--green)}
.site-header{left:0;top:4px;width:1200px;height:104px;background:var(--white)}
.brand-disc{left:148px;top:-60px;width:214px;height:240px;border-radius:0 0 107px 107px;background:var(--white);z-index:5;display:flex;align-items:flex-end;justify-content:center;padding-bottom:56px}
.brand-name{font-weight:800;color:var(--blue);font-size:25px;line-height:1.05;text-align:center;letter-spacing:.5px}
.main-nav{left:478px;top:46px;display:flex;gap:33px;font-size:14px;font-weight:600;color:var(--ink);z-index:6}
.main-nav .active{color:var(--blue)}
.login{left:938px;top:34px;width:116px;height:42px;border-radius:21px;background:var(--blue);color:var(--white);font-size:14px;font-weight:600;display:flex;align-items:center;justify-content:center;gap:7px;z-index:6}
.hero-photo{left:0;top:0;width:1200px;height:760px}
.hero-title{left:144px;top:260px;font-size:66px;font-weight:900;line-height:76px;color:var(--white);letter-spacing:1px}
.hero-sub{left:144px;top:442px;font-size:20px;font-weight:500;color:var(--white)}
.btn{display:flex;align-items:center;justify-content:center;gap:8px;border-radius:26px;color:var(--white);font-weight:700;font-size:14px;letter-spacing:.3px}
.btn-blue{background:var(--blue)}
.btn-green{background:var(--green)}
.dots{left:1116px;top:272px;display:flex;flex-direction:column;gap:11px}
.dots span{width:11px;height:11px;border-radius:50%;background:var(--white)}
.dots .on{background:var(--green)}
.kicker{font-weight:800;color:var(--ink);letter-spacing:.5px}
.kicker-sub{font-weight:700;color:var(--blue);letter-spacing:.5px}
.kicker-sub b{color:var(--green);font-weight:700}
.ghost{font-weight:900;color:var(--ghost);letter-spacing:1px}
.body-copy{font-size:14px;line-height:29.5px;color:var(--muted)}
.small-btn{height:40px;border-radius:20px;background:var(--blue);color:var(--white);font-size:12px;font-weight:700;display:flex;align-items:center;justify-content:center;gap:7px}
.svc-card{width:288px;height:350px}
.svc-photo{position:absolute;left:0;top:0;width:288px;height:190px}
.svc-panel{position:absolute;left:11px;top:163px;width:266px;height:184px;background:var(--white);box-shadow:0 6px 16px rgba(20,40,80,.14);text-align:center}
.svc-icon{position:absolute;left:111px;top:-36px;width:44px;height:44px;border-radius:50%;background:var(--white);display:flex;align-items:center;justify-content:center}
.svc-panel h3{margin-top:34px;font-size:18px;font-weight:700;color:var(--ink)}
.svc-panel p{margin:14px auto 0;width:226px;font-size:12px;line-height:21px;color:var(--muted)}
.read-link{margin-top:12px;font-size:12px;font-weight:700;color:var(--blue);display:flex;justify-content:center;align-items:center;gap:6px}
.round-arrow{width:28px;height:28px;border-radius:50%;background:#8a8f97;display:flex;align-items:center;justify-content:center}
.member{width:420px;text-align:center}
.member h3{font-size:22px;font-weight:700;color:var(--ink);letter-spacing:.5px}
.member p{margin:22px auto 0;width:340px;font-size:13px;line-height:24px;color:var(--muted)}
.proj-card{width:353px;height:388px;background:var(--white);box-shadow:0 6px 18px rgba(20,40,80,.15)}
.proj-photo{position:absolute;left:23px;top:24px;width:307px;height:165px}
.proj-card h3{position:absolute;left:25px;top:210px;font-size:19px;font-weight:700;color:var(--ink)}
.proj-card p{position:absolute;left:25px;top:246px;width:300px;font-size:12.5px;line-height:24px;color:var(--muted)}
.proj-card .small-btn{position:absolute;left:18px;top:329px;width:132px}
.field{height:52px;border:1px solid var(--line);font-size:14px;color:#555b66;padding:22px 22px 0}
.footer-nav{left:144px;top:4786px;display:flex;gap:38px;font-size:17px;font-weight:500;color:var(--white)}
.copyright{left:144px;top:4832px;font-size:11px;color:var(--white)}
.social{left:144px;top:4718px;display:flex;gap:10px}
.social span{width:40px;height:40px;border-radius:50%;border:2px solid var(--white)}
.footer-brand{left:760px;top:4708px;width:330px;text-align:center;color:var(--white);font-weight:800;font-size:52px;line-height:54px;letter-spacing:1px}
.footer-brand small{display:block;font-size:30px;line-height:36px;letter-spacing:1px}
</style>
</head>
<body>

<!-- Hero -->
<svg class="abs hero-photo" viewBox="0 0 1200 760" role="img" aria-label="Low angle view of a modern glass office building against a blue sky">
  <defs>
    <linearGradient id="heroSky" x1="0" y1="0" x2="1" y2="1">
      <stop offset="0" stop-color="#1e5ea8"/>
      <stop offset=".55" stop-color="#3f7fc2"/>
      <stop offset="1" stop-color="#7fa9d6"/>
    </linearGradient>
  </defs>
  <polygon points="0,108 1200,108 1200,570 337,758 0,568" fill="url(#heroSky)"/>
  <polyline points="85,625 337,758 985,616" fill="none" stroke="#8cc63f" stroke-width="9"/>
</svg>

<div class="abs top-rule"></div>
<div class="abs site-header"></div>
<div class="abs brand-disc"><div class="brand-name">VEL-CORA<br>SOLUTIONS</div></div>
<nav class="abs main-nav">
  <span class="active">HOME</span><span>ABOUT US</span><span>WHAT WE DO</span><span>CONTACT US</span>
</nav>
<div class="abs login">
  <svg width="12" height="13" viewBox="0 0 12 13" aria-hidden="true"><circle cx="6" cy="3.5" r="3.2" fill="#fff"/><path d="M0 13c0-4 2.6-6 6-6s6 2 6 6z" fill="#fff"/></svg>LOGIN
</div>

<h1 class="abs hero-title">VEL-CORA<br>SOLUTIONS</h1>
<p class="abs hero-sub">Lorem ipsum dolor sit ametctetur adipiscing</p>
<div class="abs btn btn-blue" style="left:144px;top:520px;width:178px;height:52px">GET STARTED
  <svg width="13" height="13" viewBox="0 0 13 13" aria-hidden="true"><circle cx="6.5" cy="6.5" r="6.5" fill="#fff"/><polyline points="5,3.5 8,6.5 5,9.5" fill="none" stroke="#0d4595" stroke-width="1.8"/></svg></div>
<div class="abs btn btn-green" style="left:330px;top:520px;width:176px;height:52px">CONTACT US
  <svg width="13" height="13" viewBox="0 0 13 13" aria-hidden="true"><circle cx="6.5" cy="6.5" r="6.5" fill="#fff"/><polyline points="5,3.5 8,6.5 5,9.5" fill="none" stroke="#8cc63f" stroke-width="1.8"/></svg></div>
<div class="abs dots"><span></span><span></span><span class="on"></span><span></span><span></span></div>

<!-- About -->
<svg class="abs" style="left:136px;top:834px" width="404" height="380" viewBox="0 0 404 380" role="img" aria-label="Photo of a modern medical office building">
  <defs><linearGradient id="aboutPh" x1="0" y1="0" x2="1" y2="1"><stop offset="0" stop-color="#2f63a8"/><stop offset=".6" stop-color="#8fa9c8"/><stop offset="1" stop-color="#b7c6d6"/></linearGradient></defs>
  <rect width="404" height="380" fill="url(#aboutPh)"/>
</svg>
<h2 class="abs kicker" style="left:606px;top:836px;font-size:46px">ABOUT</h2>
<h3 class="abs kicker-sub" style="left:606px;top:892px;font-size:37px">VEL-CORA <b>SOLUTIONS</b></h3>
<p class="abs body-copy" style="left:606px;top:960px;width:450px">Vel Cora is an investment company put together by a group of seasoned business professionals who have come together to combine decades of success in the real estate development, management, financing and medical services. The company will be a full service company offering turn key solutions for medical professionals.</p>
<div class="abs small-btn" style="left:606px;top:1167px;width:148px">READ MORE
  <svg width="12" height="12" viewBox="0 0 12 12" aria-hidden="true"><circle cx="6" cy="6" r="6" fill="#fff"/><polyline points="4.6,3.2 7.4,6 4.6,8.8" fill="none" stroke="#0d4595" stroke-width="1.6"/></svg></div>
<div class="abs ghost" style="left:40px;top:1262px;font-size:78px">ABOUT</div>

<!-- Services -->
<svg class="abs" style="left:0;top:1290px" width="1200" height="900" viewBox="0 1290 1200 900" aria-hidden="true">
  <polygon points="0,1462 862,1298 1200,1420 1200,2012 341,2182 0,2012" fill="#e9f0f9"/>
</svg>
<div class="abs ghost" style="left:752px;top:1462px;font-size:78px;color:#dde5ef">SERVICES</div>
<h2 class="abs kicker" style="left:0;width:1200px;text-align:center;top:1460px;font-size:44px">SERVICES</h2>
<h3 class="abs kicker-sub" style="left:0;width:1200px;text-align:center;top:1518px;font-size:36px">WE <b>PROVIDE</b></h3>

<div class="abs round-arrow" style="left:85px;top:1705px"><svg width="10" height="12" viewBox="0 0 10 12" aria-hidden="true"><polyline points="7,1 2,6 7,11" fill="none" stroke="#fff" stroke-width="2"/></svg></div>
<div class="abs round-arrow" style="left:1085px;top:1705px"><svg width="10" height="12" viewBox="0 0 10 12" aria-hidden="true"><polyline points="3,1 8,6 3,11" fill="none" stroke="#fff" stroke-width="2"/></svg></div>

<div class="abs svc-card" style="left:144px;top:1624px">
  <div class="svc-photo" role="img" aria-label="Photo of a hand placing light bulbs on rising steps" style="background:linear-gradient(180deg,#e4e4e2,#b9b9b6)"></div>
  <div class="svc-panel">
    <div class="svc-icon"><svg width="30" height="30" viewBox="0 0 30 30" aria-hidden="true"><circle cx="15" cy="15" r="12" fill="none" stroke="#8cc63f" stroke-width="2.5"/><line x1="15" y1="8" x2="15" y2="22" stroke="#8cc63f" stroke-width="2.5"/></svg></div>
    <h3>Conceptualization</h3>
    <p>Lorem ipsum dolor sit onsectetur adipiscing elit, sed do eiusmod tempor incididunt</p>
    <div class="read-link">READ MORE <svg width="12" height="12" viewBox="0 0 12 12" aria-hidden="true"><circle cx="6" cy="6" r="6" fill="#0d4595"/><polyline points="4.6,3.2 7.4,6 4.6,8.8" fill="none" stroke="#fff" stroke-width="1.6"/></svg></div>
  </div>
</div>
<div class="abs svc-card" style="left:457px;top:1624px">
  <div class="svc-photo" role="img" aria-label="Photo of a new commercial building under a blue sky" style="background:linear-gradient(180deg,#3d78c4,#c9d3dc)"></div>
  <div class="svc-panel">
    <div class="svc-icon"><svg width="30" height="30" viewBox="0 0 30 30" aria-hidden="true"><rect x="6" y="10" width="18" height="16" fill="none" stroke="#8cc63f" stroke-width="2.5"/><line x1="3" y1="10" x2="27" y2="10" stroke="#8cc63f" stroke-width="2.5"/></svg></div>
    <h3>Construction</h3>
    <p>Lorem ipsum dolor sit onsectetur adipiscing elit, sed do eiusmod tempor incididunt</p>
    <div class="read-link">READ MORE <svg width="12" height="12" viewBox="0 0 12 12" aria-hidden="true"><circle cx="6" cy="6" r="6" fill="#0d4595"/><polyline points="4.6,3.2 7.4,6 4.6,8.8" fill="none" stroke="#fff" stroke-width="1.6"/></svg></div>
  </div>
</div>
<div class="abs svc-card" style="left:768px;top:1624px">
  <div class="svc-photo" role="img" aria-label="Photo of financial charts on a desk" style="background:linear-gradient(180deg,#d9c9a8,#5d7596)"></div>
  <div class="svc-panel">
    <div class="svc-icon"><svg width="30" height="30" viewBox="0 0 30 30" aria-hidden="true"><rect x="4" y="6" width="22" height="18" fill="none" stroke="#8cc63f" stroke-width="2.5"/><polyline points="8,19 13,14 17,17 23,10" fill="none" stroke="#8cc63f" stroke-width="2.5"/></svg></div>
    <h3>Financing</h3>
    <p>Lorem ipsum dolor sit onsectetur adipiscing elit, sed do eiusmod tempor incididunt</p>
    <div class="read-link">READ MORE <svg width="12" height="12" viewBox="0 0 12 12" aria-hidden="true"><circle cx="6" cy="6" r="6" fill="#0d4595"/><polyline points="4.6,3.2 7.4,6 4.6,8.8" fill="none" stroke="#fff" stroke-width="1.6"/></svg></div>
  </div>
</div>

<!-- Team -->
<h2 class="abs kicker" style="left:0;width:1200px;text-align:center;top:2246px;font-size:44px">OUR</h2>
<h3 class="abs kicker-sub" style="left:0;width:1200px;text-align:center;top:2304px;font-size:36px">MANAGEMENT <b>TEAM</b></h3>
<div class="abs ghost" style="left:46px;top:2928px;font-size:78px;transform:rotate(-90deg);transform-origin:0 0;white-space:nowrap">OUR TEAM</div>

<svg class="abs" style="left:210px;top:2460px" width="320" height="290" viewBox="0 0 320 290" aria-hidden="true">
  <g fill="#0d4595"><rect x="92" y="13" width="92" height="9"/><rect x="92" y="270" width="92" height="9"/><rect x="0" y="106" width="9" height="80"/><rect x="267" y="106" width="9" height="80"/></g>
</svg>
<div class="abs" style="left:234px;top:2489px;width:234px;height:234px;border-radius:50%;background:linear-gradient(160deg,#8b8f94,#4e5560);border:4px solid #fff" role="img" aria-label="Portrait of Dr. Gil Parish"></div>
<svg class="abs" style="left:690px;top:2460px" width="320" height="290" viewBox="0 0 320 290" aria-hidden="true">
  <g fill="#0d4595"><rect x="92" y="13" width="92" height="9"/><rect x="92" y="270" width="92" height="9"/><rect x="0" y="106" width="9" height="80"/><rect x="267" y="106" width="9" height="80"/></g>
</svg>
<div class="abs" style="left:714px;top:2489px;width:234px;height:234px;border-radius:50%;background:linear-gradient(160deg,#6fa3c9,#2f5f82);border:4px solid #fff" role="img" aria-label="Portrait of Dietmar Vellasquin"></div>

<div class="abs member" style="left:148px;top:2780px">
  <h3>DR. GIL PARISH</h3>
  <p>A published author and experienced, board-certified physician in the field of Bioidentical Hormone Replacement Therapy, Dr. Parish believes in a holistic approach to helping men and women look stunning and feel great.</p>
</div>
<div class="abs member" style="left:628px;top:2780px">
  <h3>DIETMAR VELLASQUIN</h3>
  <p>Dietmar brings over 25 years of experience in partnering with dentists across Western Canada as a dental consultant.He has been involved in building hundreds of clinics and has assisted clients with clinic location and design, negotiating</p>
</div>
<div class="abs small-btn" style="left:285px;top:2982px;width:146px">READ MORE <svg width="12" height="12" viewBox="0 0 12 12" aria-hidden="true"><circle cx="6" cy="6" r="6" fill="#fff"/><polyline points="4.6,3.2 7.4,6 4.6,8.8" fill="none" stroke="#0d4595" stroke-width="1.6"/></svg></div>
<div class="abs small-btn" style="left:765px;top:2982px;width:146px">READ MORE <svg width="12" height="12" viewBox="0 0 12 12" aria-hidden="true"><circle cx="6" cy="6" r="6" fill="#fff"/><polyline points="4.6,3.2 7.4,6 4.6,8.8" fill="none" stroke="#0d4595" stroke-width="1.6"/></svg></div>

<!-- Projects -->
<svg class="abs" style="left:0;top:3120px" width="1200" height="500" viewBox="0 3120 1200 500" role="img" aria-label="Photo of a man on the phone at a construction site, tinted blue and green">
  <defs><linearGradient id="projBand" x1="0" y1="0" x2="1" y2="0"><stop offset="0" stop-color="#1f5b9f"/><stop offset=".5" stop-color="#3f8a6e"/><stop offset="1" stop-color="#8cc63f"/></linearGradient></defs>
  <polygon points="0,3307 862,3127 1200,3262 1200,3612 0,3612" fill="url(#projBand)"/>
</svg>
<div class="abs ghost" style="left:908px;top:3338px;font-size:78px;color:rgba(255,255,255,.18)">PROJE</div>
<h2 class="abs kicker" style="left:0;width:1200px;text-align:center;top:3284px;font-size:44px;color:#fff">OUR</h2>
<h3 class="abs kicker-sub" style="left:0;width:1200px;text-align:center;top:3344px;font-size:34px;color:#fff">PROPOSED PROJECTS</h3>

<div class="abs proj-card" style="left:47px;top:3472px">
  <div class="proj-photo" role="img" aria-label="Site plan drawing of the business park" style="background:linear-gradient(180deg,#f1f1f1,#cfcfcf)"></div>
  <h3>Pinegrove Business Park</h3>
  <p>Lorem ipsum dolor sit amet, consectetur adipiscing elit, sed do eiusmod tempor incididunt ut lare magna aliqua.</p>
  <div class="small-btn">READ MORE <svg width="12" height="12" viewBox="0 0 12 12" aria-hidden="true"><circle cx="6" cy="6" r="6" fill="#fff"/><polyline points="4.6,3.2 7.4,6 4.6,8.8" fill="none" stroke="#0d4595" stroke-width="1.6"/></svg></div>
</div>
<div class="abs proj-card" style="left:424px;top:3472px">
  <div class="proj-photo" role="img" aria-label="Black and white rendering of a business park building" style="background:linear-gradient(180deg,#3a3a3a,#9a9a9a)"></div>
  <h3>Holtmere Business Park</h3>
  <p>Lorem ipsum dolor sit amet, consectetur adipiscing elit, sed do eiusmod tempor incididunt ut lare magna aliqua.</p>
  <div class="small-btn">READ MORE <svg width="12" height="12" viewBox="0 0 12 12" aria-hidden="true"><circle cx="6" cy="6" r="6" fill="#fff"/><polyline points="4.6,3.2 7.4,6 4.6,8.8" fill="none" stroke="#0d4595" stroke-width="1.6"/></svg></div>
</div>
<div class="abs proj-card" style="left:800px;top:3472px">
  <div class="proj-photo" role="img" aria-label="Black and white rendering of a clinic interior" style="background:linear-gradient(180deg,#2e2e2e,#a8a8a8)"></div>
  <h3>Mt. Corwin Ridge Professional</h3>
  <p>Lorem ipsum dolor sit amet, consectetur adipiscing elit, sed do eiusmod tempor incididunt ut lare magna aliqua.</p>
  <div class="small-btn">READ MORE <svg width="12" height="12" viewBox="0 0 12 12" aria-hidden="true"><circle cx="6" cy="6" r="6" fill="#fff"/><polyline points="4.6,3.2 7.4,6 4.6,8.8" fill="none" stroke="#0d4595" stroke-width="1.6"/></svg></div>
</div>

<!-- Contact -->
<h2 class="abs kicker" style="left:0;width:1200px;text-align:center;top:3974px;font-size:44px">CONTACT</h2>
<h3 class="abs kicker-sub" style="left:0;width:1200px;text-align:center;top:4034px;font-size:36px">VEL-CORA <b>SOLUTIONS</b></h3>
<div class="abs field" style="left:233px;top:4137px;width:360px">First Name</div>
<div class="abs field" style="left:605px;top:4137px;width:360px">Last Name</div>
<div class="abs field" style="left:233px;top:4203px;width:360px">Email address</div>
<div class="abs field" style="left:605px;top:4203px;width:360px">Phone Number</div>
<div class="abs field" style="left:233px;top:4268px;width:732px;height:116px">Message</div>
<div class="abs small-btn" style="left:493px;top:4425px;width:214px;height:52px;border-radius:26px;font-size:14px">SUBMIT MESSAGE <svg width="13" height="13" viewBox="0 0 12 12" aria-hidden="true"><circle cx="6" cy="6" r="6" fill="#fff"/><polyline points="4.6,3.2 7.4,6 4.6,8.8" fill="none" stroke="#0d4595" stroke-width="1.6"/></svg></div>
<div class="abs ghost" style="left:50px;top:4476px;font-size:78px">CONTACT</div>

<!-- Footer -->
<svg class="abs" style="left:0;top:4520px" width="1200" height="362" viewBox="0 4520 1200 362" aria-hidden="true">
  <polygon points="0,4700 862,4540 1200,4606 1200,4882 0,4882" fill="#0d4595"/>
  <polyline points="218,4676 862,4530 1200,4594" fill="none" stroke="#8cc63f" stroke-width="9"/>
</svg>
<div class="abs social" aria-label="Social media links"><span></span><span></span><span></span><span></span></div>
<nav class="abs footer-nav"><span>HOME</span><span>ABOUT US</span><span>WHAT WE DO</span><span>CONTACT US</span></nav>
<p class="abs copyright">Copyright © 2020 Vel-Cora Solutions &nbsp;All rights reserved &nbsp;| &nbsp;Terms of use</p>
<div class="abs footer-brand">VEL-CORA<small>SOLUTIONS</small></div>

</body>
</html>
```